Creative, fresh business card design for Ripplecraft Facades

We need a fresh, creative business card design for Ripplecraft Facades. We are the manufacturer of Ripplecraft Facades in Australia. Wall panels are 2400 x 1200mm panels made from MDF and feature 3D patterns on the face of the panel. The colours to be used are green, silver/grey and white RGB
Red 187
Green 207
Blue 65.

An idea is to possibly use a watermark of one of our designs as a background (like on the "Grids" design on the left hand side of page 2 of our brochure).

Target Market(s)

Interior designers, architects, builders and home renovators

Industry/Entity Type

Business

Contact Information for Business Card

Details to go on the card are:
Our logo (attached),
Slogan: "Decorative panels for interiors and exteriors",
Contact name,
Position,
Mobile phone number,
Business address,
Business phone,
Business fax,
Website and
Email address.

I have attached a few images of our panels and our brochure for reference.

The colours of the business card should feature our logo colours which are: RGB
Red 187
Green 207
Blue 65

Requirements
Must have
• Very modern fonts and design. Some of the designs shown especially the "Prisms" design which is a popular design.
Nice to have
• Creative but simple design. Very contemporary.
Should not have
• Anything ornate or old fashioned.

```html
<!DOCTYPE html>
<html lang="en">
<head>
<meta charset="utf-8">
<title>Ripplecraft Facades – Business Card</title>
<link href="https://fonts.googleapis.com/css2?family=Open+Sans:wght@400;600;700&family=Arimo:wght@400;700&display=swap" rel="stylesheet">
<style>
  :root {
    --stage: #606060;
    --stage-top: #676767;
    --card-white: #f4f4f4;
    --lime: #c0d52e;
    --lime-deep: #9aad1c;
    --silver: #939598;
    --ink: #2b2b2b;
    --muted: #a4a6a8;
    --white: #ffffff;
  }
  * { margin: 0; padding: 0; box-sizing: border-box; }
  html, body { width: 1200px; height: 900px; overflow: hidden; }
  body {
    background: linear-gradient(180deg, var(--stage-top) 0%, var(--stage) 100%);
    position: relative;
    font-family: "Open Sans", Arial, sans-serif;
  }
  .card {
    position: absolute;
    top: 306px;
    width: 440px;
    height: 271px;
    border-radius: 10px;
    overflow: hidden;
    box-shadow: 0 2px 6px rgba(0,0,0,0.25);
  }
  .card-front { left: 149px; background: var(--card-white); }
  .card-back { left: 608px; background: var(--lime-deep); }

  /* Front: brand block */
  .brand {
    position: absolute;
    left: 43px;
    top: 56px;
    width: 168px;
    text-align: center;
  }
  .brand-tile {
    position: absolute;
    left: 0; top: 0;
    width: 168px; height: 74px;
    background: var(--lime);
  }
  .brand-mark {
    display: flex;
    align-items: center;
    justify-content: center;
    gap: 8px;
    background: var(--silver);
    height: 24px;
    margin-top: 79px;
  }
  .brand-square { width: 11px; height: 11px; background: var(--lime); }
  .brand-name {
    font-family: "Arimo", Arial, sans-serif;
    font-size: 15px;
    font-weight: 400;
    color: var(--white);
    letter-spacing: -0.2px;
  }
  .slogan {
    margin-top: 4px;
    margin-left: -8px;
    margin-right: -8px;
    font-family: "Arimo", Arial, sans-serif;
    font-size: 10px;
    line-height: 12.5px;
    letter-spacing: 2.3px;
    color: var(--muted);
    white-space: nowrap;
  }

  /* Front: contact block */
  .contact {
    position: absolute;
    left: 249px;
    top: 44px;
    color: var(--ink);
  }
  .person-name {
    font-family: "Arimo", Arial, sans-serif;
    font-weight: 700;
    font-size: 14px;
    color: var(--lime);
    letter-spacing: 0.2px;
    line-height: 17px;
  }
  .person-role { font-size: 11.5px; line-height: 16px; }
  .contact-list { list-style: none; margin-top: 13px; }
  .contact-list li {
    display: flex;
    align-items: center;
    gap: 6px;
    font-size: 11.5px;
    line-height: 16px;
  }
  .contact-list svg { width: 10px; height: 10px; flex: none; }
  .address { margin-top: 11px; font-size: 11.5px; line-height: 16px; }

  /* Front: footer bands */
  .footer-bands { position: absolute; left: 0; top: 228px; width: 440px; height: 43px; }
  .website {
    position: absolute;
    left: 48px;
    top: 240px;
    font-size: 11px;
    font-weight: 700;
    color: var(--white);
    white-space: nowrap;
  }

  /* Back */
  .back-logo {
    position: absolute;
    left: 50%;
    top: 50%;
    transform: translate(-50%, -50%);
    display: flex;
    align-items: center;
    gap: 12px;
  }
  .back-square { width: 22px; height: 22px; background: var(--white); }
  .back-name {
    font-family: "Arimo", Arial, sans-serif;
    font-size: 26px;
    font-weight: 400;
    color: var(--white);
    white-space: nowrap;
  }
</style>
</head>
<body>

  <section class="card card-front">
    <div class="brand">
      <div class="brand-tile" role="img" aria-label="Green brand tile"></div>
      <div class="brand-mark">
        <span class="brand-square"></span>
        <span class="brand-name">Ripplecraft Facades</span>
      </div>
      <p class="slogan">decorative panels for<br>interiors &amp; landscapes</p>
    </div>

    <div class="contact">
      <p class="person-name">MARCUS HALE</p>
      <p class="person-role">Managing Director</p>
      <ul class="contact-list">
        <li>
          <svg viewBox="0 0 10 10"><rect x="2.5" y="0.5" width="5" height="9" rx="1" fill="none" stroke="#c0d52e" stroke-width="1.2"/><rect x="4.2" y="7.3" width="1.6" height="1" fill="#c0d52e"/></svg>
          044-310 482 675
        </li>
        <li>
          <svg viewBox="0 0 10 10"><path d="M1 4 Q5 0.5 9 4 L8 5.5 L6.5 4.5 L6.5 3.6 Q5 3 3.5 3.6 L3.5 4.5 L2 5.5 Z" fill="#c0d52e"/><rect x="2" y="6" width="6" height="3" rx="0.6" fill="#c0d52e"/></svg>
          044-310 482 600
        </li>
        <li>
          <svg viewBox="0 0 10 10"><rect x="2.5" y="0.5" width="5" height="3" fill="none" stroke="#c0d52e" stroke-width="1"/><rect x="0.8" y="3.6" width="8.4" height="5.6" rx="0.8" fill="#c0d52e"/><rect x="2.8" y="5.4" width="4.4" height="1" fill="#f4f4f4"/></svg>
          044-310 482 611
        </li>
        <li>
          <svg viewBox="0 0 10 10"><rect x="0.5" y="2" width="9" height="6.5" fill="#c0d52e"/><path d="M0.8 2.3 L5 5.6 L9.2 2.3" fill="none" stroke="#f4f4f4" stroke-width="0.9"/></svg>
          hello@ripplecraft.example
        </li>
      </ul>
      <p class="address">48 Kelvin Lane, Moorfield<br>Australia, 3071.</p>
    </div>

    <svg class="footer-bands" viewBox="0 0 440 43" aria-hidden="true">
      <polygon points="0,0 212,0 247,43 0,43" fill="var(--lime)"/>
      <polygon points="234,15 440,15 440,43 254,43" fill="var(--silver)"/>
    </svg>
    <p class="website">www.ripplecraft.example</p>
  </section>

  <section class="card card-back">
    <div class="back-logo">
      <span class="back-square"></span>
      <span class="back-name">Ripplecraft Facades</span>
    </div>
  </section>

</body>
</html>
```